Unique Business Card Design

Unique Business Card design for our orthotic and prosthetic company. Our logo is on our website, color is light blue. Unique shape (artificial leg shaped, vertical, etc..) preferred. Logo, business name, individual name and basic demographics needed.

Industry/Entity Type

Business

Contact Information for Business Card

Logo, Industry, Phone # Logo, "Prosthetic & Orthotic Services" Place to add individual name and contact info

Colors
cee9f5

Requirements
Must have
• The icon must be there, placement of "Prosthetic & Orthotic Services" can be moved
Nice to have
• Like the mix of light blue, and a little darker blue. One design included the icons from my website which was a nice touch

```html
<!DOCTYPE html>
<html lang="en">
<head>
<meta charset="utf-8">
<title>Limbwell Inc. Business Card</title>
<link rel="stylesheet" href="https://fonts.googleapis.com/css2?family=Open+Sans:wght@400;600;700&family=Roboto:wght@400&family=Crimson+Text:ital@1&display=swap">
<style>
  :root {
    --brand-blue: #1560ad;
    --card-white: #ffffff;
    --text-grey: #4a4a4a;
    --backdrop: #5a4838;
    --rule-light: #d8e6f5;
  }
  * { margin: 0; padding: 0; box-sizing: border-box; }
  html, body { width: 1200px; height: 987px; overflow: hidden; }
  body { background: var(--backdrop); position: relative; font-family: "Open Sans", sans-serif; }

  .card {
    position: absolute;
    left: 293px;
    width: 615px;
    height: 352px;
    border-radius: 22px;
    overflow: hidden;
  }
  .card--front { top: 130px; background: var(--card-white); }
  .card--back { top: 506px; background: var(--brand-blue); }

  .side-band {
    position: absolute; left: 0; top: 0; bottom: 0; width: 68px;
    background: var(--brand-blue);
  }
  .mark-circle {
    position: absolute; border-radius: 50%;
  }
  .card--front .mark-circle {
    left: 22px; top: 28px; width: 90px; height: 90px;
    background: var(--card-white); border: 3px solid var(--brand-blue);
  }
  .card--back .mark-circle {
    left: 94px; top: 118px; width: 110px; height: 110px;
    background: var(--card-white);
  }

  .company-name {
    position: absolute; font-weight: 600; letter-spacing: -0.3px; white-space: nowrap;
  }
  .card--front .company-name { left: 132px; top: 38px; font-size: 26px; color: var(--brand-blue); }
  .card--back .company-name { left: 234px; top: 131px; font-size: 32px; color: var(--card-white); }

  .name-rule { position: absolute; }
  .card--front .name-rule { left: 132px; top: 74px; width: 224px; height: 2px; background: var(--brand-blue); }
  .card--back .name-rule { left: 238px; top: 171px; width: 281px; height: 5px; background: var(--card-white); }

  .tagline {
    position: absolute; font-family: "Crimson Text", serif; font-style: italic; white-space: nowrap;
  }
  .card--front .tagline { left: 148px; top: 78px; font-size: 15px; color: var(--brand-blue); }
  .card--back .tagline { left: 251px; top: 180px; font-size: 20px; color: var(--card-white); }

  .person-name {
    position: absolute; left: 141px; top: 110px;
    font-size: 21px; font-weight: 700; color: var(--brand-blue); letter-spacing: 0.3px;
  }
  .person-title {
    position: absolute; left: 141px; top: 139px;
    font-size: 14px; font-weight: 700; color: var(--brand-blue);
  }

  .contact-list {
    position: absolute; right: 26px; top: 178px; list-style: none;
    font-family: "Roboto", sans-serif; font-size: 15px; color: var(--text-grey);
  }
  .contact-list li {
    display: flex; justify-content: flex-end; align-items: center;
    height: 23.6px; gap: 10px;
  }
  .contact-list svg { width: 17px; height: 17px; fill: var(--brand-blue); flex: none; }
  .address {
    position: absolute; right: 26px; top: 304px;
    font-family: "Roboto", sans-serif; font-size: 15px; color: var(--text-grey);
  }

  .footer-url {
    position: absolute; left: 0; right: 0; top: 298px;
    display: flex; align-items: center; justify-content: center; gap: 8px;
    font-family: "Roboto", sans-serif; font-size: 14px; color: var(--card-white);
  }
  .footer-url .fade-line { height: 1px; width: 120px; }
  .fade-line--left { background: linear-gradient(to right, transparent, var(--rule-light)); }
  .fade-line--right { background: linear-gradient(to left, transparent, var(--rule-light)); }
</style>
</head>
<body>

<section class="card card--front">
  <div class="side-band"></div>
  <div class="mark-circle"></div>
  <div class="company-name">LIMBWELL INC.</div>
  <div class="name-rule"></div>
  <div class="tagline">Prosthetic &amp; Orthotic Services</div>
  <div class="person-name">MIRA KESTEL</div>
  <div class="person-title">CO LPO</div>

  <ul class="contact-list">
    <li>555.010.1700
      <svg viewBox="0 0 20 20" aria-hidden="true"><path d="M2 7c0-3 4-4 8-4s8 1 8 4v2h-4V7H6v2H2z"/><path d="M5 10l2-3h6l2 3v6H5z"/><circle cx="10" cy="12.5" r="1.8" fill="#fff"/></svg>
    </li>
    <li>555.010.3919
      <svg viewBox="0 0 20 20" aria-hidden="true"><rect x="5" y="1" width="10" height="18" rx="2"/><rect x="7" y="4" width="6" height="10" fill="#fff"/><circle cx="10" cy="16.5" r="1" fill="#fff"/></svg>
    </li>
    <li>555-0195415
      <svg viewBox="0 0 20 20" aria-hidden="true"><rect x="5" y="2" width="10" height="6"/><rect x="2" y="8" width="16" height="7" rx="1"/><rect x="5" y="13" width="10" height="5"/><rect x="6" y="14.5" width="8" height="1" fill="#fff"/></svg>
    </li>
    <li>Mkestel@limbwellinc.com
      <svg viewBox="0 0 20 20" aria-hidden="true"><rect x="2" y="5" width="16" height="11"/><path d="M2 5l8 6 8-6" fill="none" stroke="#fff" stroke-width="1.5"/></svg>
    </li>
    <li>www.limbwellinc.com
      <svg viewBox="0 0 20 20" aria-hidden="true"><circle cx="10" cy="10" r="8"/><path d="M6 5c2 1 3 3 2 5s1 3 3 3M12 4c0 2 2 3 4 3" fill="none" stroke="#fff" stroke-width="1.4"/></svg>
    </li>
  </ul>
  <div class="address">2204 Harbor Ave., Riverton, NY 10988</div>
</section>

<section class="card card--back">
  <div class="mark-circle"></div>
  <div class="company-name">LIMBWELL INC.</div>
  <div class="name-rule"></div>
  <div class="tagline">Prosthetic &amp; Orthotic Services</div>
  <div class="footer-url">
    <span class="fade-line fade-line--left"></span>
    www.limbwellinc.com
    <span class="fade-line fade-line--right"></span>
  </div>
</section>

</body>
</html>
```